Looking for a cool, modern Cannabis Jar Label

I want you to come up with a better, modern look for a label.

I need it sized to 4” x 3” - I plan to print directly to label printer.

I want you to use Photoshop and deliver me a layered PSD file that I can edit and modify the information as needed..

The label information will need to include places for:
(1) Strain Name - most important part of label - larger font size than rest - example Kestrel Mist, PLV #7, Juniper Hollow
(2) Pricing - for Gram, 1/8, 1/4, 1/2. and Ounce
(3) Strain Designation (Hybrid, Indica or Sativa) - maybe color coded, different color for Indica v. Sativa, just an idea
(4) THC and CBD percentages - for example 23% THC and 0.05% CBD
(5) Farm name - a place where we can add the name/logo of the business that produced the product. example - Ovenrow Farms

I have attached a simple mockup showing the information.

I have also attached a few samples of labels we like to give you an idea of the look and feel we are going for.

I am wanting a very clean, modern, classy, readable look.The font will use is Gotham Font.

HI Everyone! Thank you for all of your designs. I am requesting an extension because I need more time to give adequate feedback to the designers. Thank you for your participation and all of your efforts! I will be making a decision soon!

• Gotham Font

• Thank you for your designs. I am sorry i have been slow in providing feedback, things have been really busy around here!
• I wanted to give some group general feedback. After reviewing all of the designs, there is a common theme among all of the designs that I would like to see changed.
• I would like to see the per gram pricing more prominent on the label. This is what most people are looking for when they are purchasing the product. So I would like to see this stand out from the other pricing tiers. As I think about it, they don't all need to be grouped together in a line. You could have the Per Gram pricing front and center some where and then the other pricing tiers grouped together somewhere else on the label.
• This is the order of importance of items on the label. Items at the the top of the list should be bigger than those below it.
• 1. Strain name
• 2. Pricing - being per gram the most important of all prices
• 3. THC/CBD percentages
• 4. Strain Type (indica, sativa, hybrid)
• 5. Farm name/logo
• When laying out these labels, they will be going on rounded jars and they will be on display. Think of jars with fancy labels in a candy store. They need to be eye catchy, appealing, but easy read.
• Thank you for all of your hard work, everyone is doing a great job.
• Best,
• Neta

```html
<!DOCTYPE html>
<html lang="en">
<head>
<meta charset="utf-8">
<title>Kestrel Mist – Jar Label</title>
<link rel="stylesheet" href="https://fonts.googleapis.com/css2?family=Montserrat:wght@400;500;700&family=Oswald:wght@300;400&display=swap">
<style>
  :root {
    --backdrop: #4d4d4d;
    --label: #ffffff;
    --green: #196b2e;
    --ink: #000000;
    --muted: #555555;
    --rule: #222222;
    --divider: #9a9a9a;
    --farm-ink: #333333;
    --farm-mark: #f2a12a;
  }
  * { box-sizing: border-box; margin: 0; padding: 0; }
  html, body {
    width: 1200px; height: 1200px; overflow: hidden;
    background: var(--backdrop);
  }
  .canvas { position: relative; width: 1200px; height: 1200px; }
  .label {
    position: absolute; left: 110px; top: 232px;
    width: 978px; height: 735px;
    background: var(--label);
    font-family: "Montserrat", sans-serif;
  }
  .strain-name {
    position: absolute; left: 18px; top: 16px;
    width: 943px; height: 214px;
    border: 5px solid var(--green); border-radius: 36px;
    display: flex; align-items: center; justify-content: center;
    font-size: 100px; font-weight: 400; color: var(--ink);
    letter-spacing: 1px;
  }
  .price-tier {
    position: absolute; top: 252px; width: 220px;
    transform: translateX(-50%);
    text-align: center;
  }
  .price {
    font-family: "Oswald", sans-serif; font-weight: 400;
    font-size: 80px; line-height: 1; color: var(--ink);
    letter-spacing: -3px;
    transform: scaleX(0.82); display: inline-block;
  }
  .price sup {
    font-size: 36px; vertical-align: top; position: relative; top: 2px;
    letter-spacing: -1px;
  }
  .tier-name {
    font-size: 34px; color: var(--muted); margin-top: 8px;
  }
  .potency {
    position: absolute; left: 19px; top: 457px;
    width: 340px; height: 254px;
  }
  .potency-head {
    height: 71px; background: var(--ink); color: var(--label);
    border-radius: 16px 16px 0 0;
    display: flex;
  }
  .potency-head span, .potency-values span {
    flex: 1; display: flex; align-items: center; justify-content: center;
  }
  .potency-head span { font-size: 31px; font-weight: 700; padding-top: 10px; }
  .potency-head span:first-child { border-right: 2px solid var(--divider); }
  .potency-values { height: 112px; display: flex; }
  .potency-values span {
    font-family: "Oswald", sans-serif; font-weight: 300;
    font-size: 80px; color: var(--ink); letter-spacing: -3px;
  }
  .potency-values span:first-child { border-right: 2px solid var(--divider); margin: 0 0 10px; }
  .potency-values small { font-size: 44px; margin-left: 2px; }
  .strain-type {
    height: 71px; background: var(--green); color: var(--label);
    border-radius: 0 0 16px 16px;
    display: flex; align-items: center; justify-content: center;
    font-size: 43px; letter-spacing: 1px;
  }
  .farm {
    position: absolute; left: 386px; top: 461px; width: 570px; height: 252px;
    border-top: 1.5px solid var(--rule); border-bottom: 1.5px solid var(--rule);
  }
  .farm-tag {
    position: absolute; left: 120px; top: 0; width: 254px; height: 36px;
    background: var(--ink); color: var(--label);
    border-radius: 0 0 10px 10px;
    display: flex; align-items: center; justify-content: center;
    font-size: 23px; font-weight: 500;
  }
  .farm-name {
    position: absolute; left: 0; right: 0; top: 78px;
    display: flex; align-items: center; justify-content: center; gap: 22px;
  }
  .farm-mark { width: 84px; height: 84px; border-radius: 12px; background: var(--farm-mark); }
  .farm-name span { font-size: 52px; font-weight: 700; color: var(--farm-ink); }
  .harvest-date {
    position: absolute; left: 164px; bottom: 10px;
    font-size: 23px; color: var(--ink);
  }
</style>
</head>
<body>
<main class="canvas">
  <section class="label">
    <h1 class="strain-name">Kestrel Mist</h1>

    <div class="price-tier" style="left:90px"><div class="price">€10<sup>.50</sup></div><div class="tier-name">Gram</div></div>
    <div class="price-tier" style="left:266px"><div class="price">€35<sup>.00</sup></div><div class="tier-name">1/8</div></div>
    <div class="price-tier" style="left:442px"><div class="price">€70<sup>.00</sup></div><div class="tier-name">1/4</div></div>
    <div class="price-tier" style="left:640px"><div class="price">€140<sup>.00</sup></div><div class="tier-name">1/2</div></div>
    <div class="price-tier" style="left:860px"><div class="price">€280<sup>.00</sup></div><div class="tier-name">Ounce</div></div>

    <div class="potency">
      <div class="potency-head"><span>THC</span><span>CBD</span></div>
      <div class="potency-values"><span>23<small>%</small></span><span>0.5<small>%</small></span></div>
      <div class="strain-type">INDICA</div>
    </div>

    <div class="farm">
      <div class="farm-tag">Cultivated By:</div>
      <div class="farm-name"><div class="farm-mark"></div><span>Verdel Grow</span></div>
      <div class="harvest-date">Harvested Date:</div>
    </div>
  </section>
</main>
</body>
</html>
```